Web design for Crowdfunding site HopeWingsRally.com

We need a web design for christian crowdfunding website. Here is the challenge: We need responsive layout that is targeted first in iPad size of screen. It should also scale somehow down to iPhone size of screens. Web layout can be about the same size as iPad screen.

Screens should work so that main page scrolls not but only certain part of the screen scrolls and always one "page" at time. We can implement these "scrolls" then later with javascript but now we need only design. The challenge is to create this kind of hybrid website / app look.

Target is at first to raise funds to orphan people needing about $40 per month for their living and education. There is always some organization which takes care of these kids. Later there will be other christian missions included. At first we are looking to find monthly supporters.

You can be as creative as you want :) As you see from the look and feel sector, I am not looking any same traditional look which many "help kids" sites have. I am looking to reach now younger generation and therefore iPad and mobile are the main screen sizes.

Inspirational designs:
- https://example-gallery.test/profiles/studiofernlake/designs/482716?from=%2Fbrowse%2Fxhr%2Fdesigns%3Fcategory%3Dmobile-app-design
- http://www.artpoolhub.test/design/8261047 Clear, simple visuals
- http://www.artpoolhub.test/design/7394215 Header
- http://www.artpoolhub.test/design/6048392 Contrast in the colors, i think is powerfull

Some terms could be: Kids play, kids are learning (in the school). No static posture but living like kids are. I wonder also how we could also add little bit gaming style even though the question is of reali life of real people. Giving should be rewarding.

Target Market(s)

People who want help other people.

Industry/Entity Type

Christian

Number of Pages Required

4 page

Requirements
Must have
• Homepage. Mission page (In my wireframes it was one kid).
Nice to have
• Other pages and some idea how to scroll. 4 pages is no must. If you feel easy, please give first some draft and I give comments on that.

```html
<!DOCTYPE html>
<html lang="en">
<head>
<meta charset="utf-8">
<title>HopeWingsRally – Mission</title>
<link rel="stylesheet" href="https://fonts.googleapis.com/css2?family=Montserrat:wght@400;500;600;700&display=swap">
<style>
  :root {
    --ink: #111111;
    --grey: #8e8e8e;
    --grey-light: #f2f2f2;
    --yellow: #f7b500;
    --red: #e8272d;
    --white: #ffffff;
    --icon: #9b9b9b;
    --photo-dark: #2f2f2f;
    --photo-mid: #6e6e6e;
    --photo-light: #c4c4c4;
  }
  * { margin: 0; padding: 0; box-sizing: border-box; }
  html, body { width: 1200px; height: 900px; overflow: hidden; background: var(--white); }
  body { font-family: "Montserrat", Arial, sans-serif; color: var(--ink); }
  .screen { position: relative; width: 1200px; height: 900px; overflow: hidden; background: var(--white); }

  .topbar { position: absolute; left: 0; top: 0; width: 1200px; height: 76px; background: var(--grey-light); z-index: 2; }
  .menu-toggle { position: absolute; left: 30px; top: 20px; display: flex; align-items: center; gap: 10px;
    font-size: 20px; font-weight: 600; color: var(--grey); letter-spacing: 0.2px; text-decoration: none; }
  .brand { position: absolute; left: 0; right: 0; top: 16px; text-align: center; font-size: 37px;
    font-weight: 500; color: var(--ink); letter-spacing: 0.3px; }
  .auth { position: absolute; top: 15px; height: 34px; width: 96px; border-radius: 3px; font-size: 15px;
    font-weight: 500; color: var(--white); display: flex; align-items: center; justify-content: center; text-decoration: none; }
  .auth--login { left: 969px; background: var(--ink); }
  .auth--signup { left: 1078px; background: var(--red); }

  .hero-photo { position: absolute; left: 686px; top: 76px; width: 514px; height: 590px;
    background:
      linear-gradient(to bottom, rgba(255,255,255,0) 72%, var(--white) 100%),
      linear-gradient(to right, var(--white) 0%, rgba(255,255,255,0) 14%),
      linear-gradient(150deg, var(--photo-light) 0%, var(--photo-mid) 30%, var(--photo-dark) 55%, var(--photo-mid) 80%, var(--photo-light) 100%); }

  .family-icon { position: absolute; left: 80px; top: 141px; width: 110px; height: 117px; }

  .pitch { position: absolute; left: 59px; top: 278px; font-size: 52px; font-weight: 500; line-height: 62px; letter-spacing: -0.3px; }
  .pitch .accent-yellow { color: var(--yellow); }
  .pitch .accent-grey { color: var(--grey); }
  .pitch-close { position: absolute; left: 54px; top: 530px; font-size: 88px; font-weight: 500; color: var(--red); letter-spacing: -0.5px; line-height: 1; white-space: nowrap; }
  .pledge { position: absolute; left: 58px; top: 636px; font-size: 32px; font-weight: 500; color: var(--grey); }

  .footer-note { position: absolute; left: 0; top: 826px; width: 436px; height: 74px; background: var(--grey-light);
    display: flex; align-items: center; padding-left: 48px; gap: 6px; font-size: 17px; font-weight: 500; color: #333; }
  .footer-note .copy-mark { color: var(--red); font-size: 20px; }
  .footer-note a { color: var(--red); text-decoration: none; }
  .page-code { position: absolute; left: 1127px; top: 846px; font-size: 12px; font-weight: 600; color: #333; }
</style>
</head>
<body>
<main class="screen">
  <header class="topbar">
    <a class="menu-toggle" href="#">
      <svg width="34" height="18" viewBox="0 0 34 18" aria-hidden="true">
        <g fill="#9b9b9b">
          <rect x="0" y="0" width="5" height="3"/><rect x="8" y="0" width="26" height="3"/>
          <rect x="0" y="7" width="5" height="3"/><rect x="8" y="7" width="26" height="3"/>
          <rect x="0" y="14" width="5" height="3"/><rect x="8" y="14" width="26" height="3"/>
        </g>
      </svg>
      SEE THE MISSIONS
    </a>
    <div class="brand">HOPEWINGSRALLY</div>
    <a class="auth auth--login" href="#">LOGIN</a>
    <a class="auth auth--signup" href="#">SIGN UP</a>
  </header>

  <div class="hero-photo" role="img" aria-label="Black and white photo of two clasped hands, one dark-skinned and one light-skinned"></div>

  <svg class="family-icon" viewBox="0 0 110 117" aria-hidden="true" fill="none" stroke="var(--icon)" stroke-width="4" stroke-linejoin="round" stroke-linecap="round">
    <polyline points="4,38 55,4 106,38"/>
    <line x1="84" y1="4" x2="84" y2="20"/>
    <circle cx="32" cy="40" r="11"/>
    <circle cx="78" cy="50" r="10"/>
    <circle cx="55" cy="68" r="9"/>
    <path d="M10 100 V74 a10 10 0 0 1 10 -10 h24"/>
    <path d="M100 100 V80 a10 10 0 0 0 -10 -10 h-10"/>
    <path d="M38 114 V92 a8 8 0 0 1 8 -8 h18 a8 8 0 0 1 8 8 V114"/>
  </svg>

  <p class="pitch">
    “ She has a <span class="accent-yellow">NAME</span>,<br>
    He Has a <span class="accent-grey">DREAM</span>.<br>
    She Hopes She would<br>
    have a <span class="accent-yellow">FUTURE</span>
  </p>
  <p class="pitch-close">He is Like You”.</p>
  <p class="pledge">1 USD a month will help her and him</p>

  <footer class="footer-note">
    <span class="copy-mark">©</span> Copyright 2016, <a href="#">www.companyname.com</a>
  </footer>
  <span class="page-code">M1</span>
</main>
</body>
</html>
```